KRT Project Signage

Need a sign to be displayed in the front of properties currently under Construction or Renovation to advertise our company information. Need it to be Professional and Contemporary. We are a Design/Build Construction Company. Information should include Company Name, email, website, phone number. Attached: Logo and company brochure, also included and inspiration images

```html
<!DOCTYPE html>
<html lang="en">
<head>
<meta charset="utf-8">
<title>KRT Construction – Project Sign</title>
<link href="https://fonts.googleapis.com/css2?family=Montserrat:wght@500;600;700&display=swap" rel="stylesheet">
<style>
  :root {
    --backdrop: #262626;
    --panel-white: #ffffff;
    --panel-black: #000000;
    --accent: #f2e943;
    --ink: #111111;
    --text-light: #ffffff;
  }
  * { margin: 0; padding: 0; box-sizing: border-box; }
  html, body {
    width: 1200px; height: 1200px; overflow: hidden;
    background: var(--backdrop);
    font-family: "Montserrat", sans-serif;
  }
  .sign {
    position: absolute; left: 250px; top: 75px;
    width: 700px; height: 1049px;
  }
  .brand-panel {
    height: 515px; background: var(--panel-white);
    display: flex; flex-direction: column; align-items: center; justify-content: center;
    gap: 18px;
  }
  .brand-name {
    display: flex; align-items: center; gap: 16px;
    font-size: 52px; font-weight: 600; letter-spacing: 3px; color: var(--ink);
  }
  .brand-dot { width: 28px; height: 28px; border-radius: 50%; background: var(--accent); }
  .brand-tagline {
    font-size: 24px; font-weight: 500; letter-spacing: 5px; color: var(--ink);
  }
  .contact-panel {
    height: 534px; background: var(--panel-black);
    display: flex; flex-direction: column; align-items: center;
    padding-top: 16px;
  }
  .address {
    position: relative; color: var(--text-light); font-weight: 600;
    font-size: 37px; line-height: 44px; text-align: center; letter-spacing: 0.5px;
  }
  .address .icon { position: absolute; left: -42px; top: 4px; }
  .label {
    margin-top: 22px; border: 2px solid var(--accent); border-radius: 8px;
    color: var(--accent); font-weight: 600; font-size: 36px; line-height: 44px;
    padding: 1px 12px;
  }
  .label + .phone { margin-top: 0; }
  .phone {
    color: var(--accent); font-weight: 700; font-size: 76px; line-height: 88px;
    letter-spacing: -1px;
  }
  .phone.office { margin-bottom: 4px; }
  .web-row {
    display: flex; align-items: center; gap: 14px;
    color: var(--text-light); font-weight: 500; font-size: 38px; line-height: 56px;
  }
  .web-row.site { font-weight: 700; }
  .highlight { color: var(--accent); }
</style>
</head>
<body>
  <main class="sign">
    <section class="brand-panel">
      <div class="brand-name"><span class="brand-dot"></span>KRT CONSTRUCTION</div>
      <div class="brand-tagline">LUXURY RENOVATIONS</div>
    </section>
    <section class="contact-panel">
      <address class="address" style="font-style:normal">
        <svg class="icon" width="26" height="30" viewBox="0 0 26 30" aria-hidden="true">
          <path d="M13 2a8 8 0 0 0-8 8c0 6 8 13 8 13s8-7 8-13a8 8 0 0 0-8-8z" fill="var(--accent)"/>
          <circle cx="13" cy="10" r="3" fill="#000"/>
          <ellipse cx="13" cy="25" rx="10" ry="3" fill="none" stroke="var(--accent)" stroke-width="2"/>
        </svg>
        4410 NW 5TH AVE., STE. 310<br>PALM CREST, FL 33402
      </address>
      <div class="label">DIRECT</div>
      <div class="phone">555.201.3348</div>
      <div class="label">OFFICE</div>
      <div class="phone office">555.201.7720</div>
      <div class="web-row">
        <svg width="28" height="26" viewBox="0 0 28 26" aria-hidden="true">
          <rect x="2" y="8" width="24" height="16" fill="var(--accent)"/>
          <path d="M2 24l12-9 12 9" fill="none" stroke="#000" stroke-width="2"/>
          <rect x="7" y="2" width="14" height="12" fill="var(--accent)" stroke="#000" stroke-width="1.5"/>
          <path d="M10 6h8M10 9h8" stroke="#000" stroke-width="1.5"/>
        </svg>
        dana@krtconstruction.com
      </div>
      <div class="web-row site">
        <svg width="28" height="28" viewBox="0 0 28 28" aria-hidden="true">
          <g fill="none" stroke="var(--accent)" stroke-width="2">
            <circle cx="14" cy="14" r="11"/>
            <ellipse cx="14" cy="14" rx="5" ry="11"/>
            <path d="M3 14h22M5 8h18M5 20h18"/>
          </g>
        </svg>
        <span>www.<span class="highlight">krtconstruction</span>.com</span>
      </div>
    </section>
  </main>
</body>
</html>
```